Dental Website offering Continuing Educational Courses

Need a Wordpress CMS design for a dentist website which will offer continuing education courses. The design should be professional, simple and elegant. Logo versions are provided. Please follow those colors plus one or two others that will blend well. Here's examples of other sites they like - www.pulpvantage.com, www.kqtorvi.com, www.thebrightwellinstitute.com., www.plqma.org/. Please provide designs in jpg format. If selected, then final design will be required in psd format.

Target Market(s)

dentists, endodontists (root canal specialists)

Industry/Entity Type

Education

Requirements
Must have
• Combination Horizontal / Vertical navigation. Place course titles in vertical nav in a side bar on home page. List them as Course 1, Course 2 ,etc.. total of 7 courses. The header horizontal nav should be; Home, About, Courses, Doctor Name, Faculty, FAQ, Patients, Contact.
Need placeholder to accommodate one large static image just under main nav. Need web safe fonts. Need placeholder for calendar like this example www.quietharbors.org/. Need to show a dropdown menu example. Design for 1024 x 768. Need space on home page to allow for logos of external websites/ associations. These are; www.truefieldpulp.com, www.mavolix.com, www.wfk.org/, www.kintovarhq.com/kinto/. Would like to see a row of images across the bottom of the home page like the www.plqma.org site has. Would like to show a Contact Form on the home page like the "need assistance" form example on www.thebrightwellinstitute.com. Would like to create a placeholder on the home page for an image of a doctor.
Nice to have
• 3 or 4 column footer (which features sitemap, copyright, etc..). Examples in the design for the web site’s copy styling:
o through headers
o Bulleted list
o Hyperlink
o Table

```html
<!DOCTYPE html>
<html lang="en">
<head>
<meta charset="utf-8">
<title>Arcwell Dental Learning</title>
<link href="https://fonts.googleapis.com/css2?family=Arimo:wght@400;700&family=Tinos:ital,wght@0,400;0,700;1,400&display=swap" rel="stylesheet">
<style>
:root{
  --navy:#0a3d73;
  --blue:#0d58a6;
  --bright:#1f72c7;
  --deep:#082f5c;
  --foot:#0f3a6a;
  --footcol:#1565bd;
  --page:#ffffff;
  --bg:#e9eef3;
  --text:#8a8a8a;
  --dark:#333;
  --green:#6f9a2c;
  --line:#d8dde3;
}
*{margin:0;padding:0;box-sizing:border-box}
html,body{width:1050px;height:1200px;overflow:hidden}
body{position:relative;background:var(--bg);font-family:Arimo,Arial,sans-serif;color:var(--text)}
.abs{position:absolute}
.bottom-band{left:0;top:965px;width:1050px;height:235px;background:var(--foot)}
.page-column{left:151px;top:0;width:751px;height:1200px;background:var(--page)}
.page-column-foot{left:151px;top:957px;width:751px;height:243px;background:var(--footcol)}
.topline{left:0;top:0;width:1050px;height:5px;background:#555}
/* main nav */
.main-nav{left:151px;top:6px;width:751px;height:31px;background:var(--navy);display:flex}
.main-nav a{color:#fff;text-decoration:none;font-size:12px;display:flex;align-items:center;justify-content:center;border-right:1px solid #2a5b90;height:100%}
.main-nav a.on{background:var(--bright)}
.dropdown{left:305px;top:37px;width:101px;height:99px;background:var(--bright);padding:6px 0 0 24px}
.dropdown a{display:block;color:#fff;font-size:10px;font-weight:700;line-height:18px;text-decoration:none}
.dropdown a.on{text-decoration:underline}
/* header */
.header{left:161px;top:47px;width:729px;height:88px;background:var(--blue)}
.brand{left:172px;top:63px;display:flex;align-items:center;gap:8px;color:#fff;font-family:Arimo,Arial,sans-serif;font-weight:700;font-size:22px}
.brand i{display:block;width:18px;height:18px;background:#fff}
.call{left:716px;top:70px;color:#fff;font-family:Tinos,serif;text-align:left}
.call small{display:block;font-size:12px}
.call b{font-weight:400;font-size:27px;letter-spacing:1px}
/* hero */
.hero{left:161px;top:145px;width:729px;height:213px;background:linear-gradient(90deg,#8a4a2a 0%,#d9a07c 35%,#e9c3a6 55%,#c98c64 75%,#7a4a34 100%)}
.side-menu{left:161px;top:145px;width:153px;height:213px;background:var(--blue)}
.side-menu a,.sub-menu a{display:flex;align-items:center;height:23.4px;color:#cfe0f2;font-size:14px;text-decoration:none;padding-left:14px;border-bottom:1px solid #0b4c8e}
.side-menu a::before,.sub-menu a::before{content:"›";color:#fff;font-size:18px;width:30px}
.side-menu a.on{background:var(--deep);color:#fff}
.sub-menu{left:315px;top:173px;width:125px;height:129px;background:var(--blue);padding:3px 5px}
.sub-menu a{height:23.4px;border:0;padding-left:6px}
.sub-menu a.on{background:var(--bright);color:#fff}
.finder{left:658px;top:234px;width:200px;height:67px;background:var(--deep);padding:6px 12px}
.finder h3{color:#fff;font-weight:400;font-size:17px;display:flex;align-items:center;gap:10px}
.finder select{margin-top:5px;width:176px;height:25px;font-size:9px;color:#888;border:0;border-radius:2px;padding-left:4px}
.news{left:161px;top:358px;width:729px;height:42px;background:#dde3e9;display:flex;align-items:center}
.news b{color:var(--navy);font-weight:400;font-size:14px;width:118px;text-align:center}
.news span{font-size:9px;color:#555}
/* welcome */
h2.welcome{left:163px;top:424px;color:var(--blue);font-size:19px;font-weight:400}
.welcome-text{left:161px;top:455px;width:305px;font-size:9px;line-height:14.5px}
.doctor{left:480px;top:446px;width:165px;height:110px;background:linear-gradient(120deg,#4d6d9a,#c8b9a8 55%,#eee);border:1px solid #ccc;box-shadow:0 2px 4px #999}
.readmore{left:563px;top:609px;width:71px;height:23px;background:linear-gradient(#fff,#e4e4e4);border:1px solid #ccc;border-radius:3px;color:var(--navy);font-size:9px;font-weight:700;display:flex;align-items:center;justify-content:center}
.divider{left:151px;top:645px;width:510px;height:1px;background:#e7e7e7}
.vdivider{left:660px;top:400px;width:1px;height:430px;background:#e7e7e7}
/* calendar */
.cal{left:688px;top:412px;width:179px;border-collapse:collapse;font-size:9px}
.cal caption{background:#222;color:#fff;height:26px;line-height:26px;font-weight:700;font-size:11px;border-radius:3px 3px 0 0}
.cal th{background:#ececec;color:#777;font-size:7.5px;height:13px}
.cal td{width:25.5px;height:25px;text-align:center;background:#f3f3f3;border:1px solid #fff;color:#333;font-weight:700}
.cal td.off{color:#bbb}
.cal td.today{background:#555;color:#fff}
.cal td.sel{background:#ddd}
/* assistance */
.assist{left:674px;top:597px;width:210px;height:223px;border:1px solid #dde3e9}
.assist h3{font-family:Tinos,serif;color:var(--navy);font-size:15px;height:26px;padding-left:15px;background:linear-gradient(#fff,#eef1f4);border-bottom:1px solid #dde3e9;line-height:26px}
.field{position:absolute;left:10px;font-size:9px;color:#444}
.input{position:absolute;left:60px;width:143px;height:16px;border:1px solid #dde3e9}
.submit{left:817px;top:794px;width:57px;height:18px;background:var(--green);color:#fff;font-size:9px;font-weight:700;display:flex;align-items:center;justify-content:center}
/* testimonials */
.sec-title{font-family:Tinos,serif;color:var(--navy);font-size:16px}
.quote{left:168px;top:695px;width:216px;height:98px;background:#eaeaea;border-radius:3px;padding:12px 10px;font-family:Tinos,serif;font-style:italic;font-size:12px;color:#444;line-height:17px}
.quote-by{left:320px;top:800px;font-size:9px;color:#333;line-height:12px}
.quote-by i{font-size:10px}
.events{left:419px;top:664px;width:210px;height:149px;border:1px solid #dde3e9}
.events h3{height:26px;line-height:26px;padding-left:15px;font-weight:400;background:linear-gradient(#fff,#eef1f4);border-bottom:1px solid #dde3e9}
.event{position:absolute;left:6px;display:flex;gap:10px}
.event .thumb{width:64px;height:44px;background:linear-gradient(#b14b55,#f1d6d2 60%,#e9e4df)}
.event p{font-size:8px;line-height:14px;width:120px}
/* universities */
.unis{left:167px;top:834px;width:717px;height:106px;border:1px solid #cfd6de}
.unis-tab{left:169px;top:836px;width:28px;height:102px;background:var(--green);color:#fff;font-family:Tinos,serif;font-size:12px;writing-mode:vertical-rl;transform:rotate(180deg);text-align:center;letter-spacing:1px}
.badge{position:absolute;top:850px;width:100px;height:72px;background:#e3e6ea;border-radius:4px}
/* footer */
.footer-panel{left:166px;top:978px;width:720px;height:117px;background:var(--blue);border:1px solid #2b7ad0;border-radius:4px}
.fcol{position:absolute;top:990px}
.fcol h4{color:#fff;font-size:10px;font-weight:700;margin-bottom:18px}
.fcol a,.fcol p{display:block;color:#9ec2ea;font-size:9px;line-height:15.5px;text-decoration:none}
.social{position:absolute;width:22px;height:22px;border-radius:50%}
.foot-links{left:185px;top:1095px;width:687px;height:37px;background:var(--deep);display:flex;justify-content:center;align-items:center;gap:16px;color:#bcd4ee;font-size:9px}
.copy{left:151px;top:1148px;width:751px;text-align:center;color:#bcd4ee;font-size:9px}
</style>
</head>
<body>
<div class="abs bottom-band"></div>
<div class="abs page-column"></div>
<div class="abs page-column-foot"></div>
<div class="abs topline"></div>

<nav class="abs main-nav">
  <a style="width:56px">HOME</a><a style="width:75px">ABOUT</a><a class="on" style="width:102px">COURSES</a><a style="width:120px">DOCTOR NAME</a><a style="width:90px">FACULTY</a><a style="width:68px">FAQ</a><a style="width:98px">PATIENTS</a><a style="width:142px;border:0">CONTACT</a>
</nav>

<header class="abs header"></header>
<div class="abs brand"><i></i>Arcwell Dental</div>
<div class="abs call"><small>CALL FOR INQUIRIES!</small><b>555 014 2290</b></div>
<div class="abs dropdown"><a>Course 1</a><a class="on">Course 2</a><a>Course 3</a><a>Course 4</a><a>Course 5</a></div>

<div class="abs hero" role="img" aria-label="Photo of smiling students and dentists"></div>
<nav class="abs side-menu">
  <a>Course 1</a><a class="on">Course 2</a><a>Course 3</a><a>Course 4</a><a>Course 5</a><a>Course 6</a><a>Course 7</a><a>Course 8</a><a>Course 9</a>
</nav>
<nav class="abs sub-menu"><a>Course 1</a><a class="on">Course 2</a><a>Course 3</a><a>Course 4</a><a>Course 5</a></nav>
<div class="abs finder">
  <h3><svg width="18" height="18" viewBox="0 0 18 18"><circle cx="11" cy="7" r="5" fill="none" stroke="#ccc" stroke-width="2"/><line x1="7" y1="11" x2="2" y2="16" stroke="#ccc" stroke-width="2.5"/></svg>FIND A COURSE</h3>
  <select><option>Choose a track</option></select>
</div>
<div class="abs news"><b>NEWS:</b><span>Lorem ipsum dolor sit amet, consectetuer adipiscing elit. Aenean commodo ligula eget dolor.Lorem ipsum dolor sit amet,</span></div>

<h2 class="abs welcome">WELCOME</h2>
<p class="abs welcome-text">Lorem ipsum dolor sit amet, consectetuer adipiscing elit. Aeneacommodo ligula eget dolor.Lorem ipsum dolor sit amet, consectetuer adipiscing elit. AenLorem ipsum dolor sitmet, consectetuer adipiscing elit. ean commodo ligula eget dolor.ean commodo ligulat dolor.Loreor sit amet, consectetuer adipiscing elit. Aenean commodo liguleglorem, consectetuer adipiscing elit. Aenean commodo ligula eget doLorem ipsum dolor sit amet, coscing elit. Aenean commodo ligula eget dolor.lor.g elit. Aenean commodo ligula eget dolorLorem ipsum dolor sit amet, cctetuer adipiscing elit. AeLoLorem ipsuing elit. Aenean commoan commodo ligula eget dolor.ean commodo ligulat dolor.Lorem ipsum dolor sit amet,</p>
<div class="abs doctor" role="img" aria-label="Photo of a doctor examining a young patient"></div>
<div class="abs readmore">Read more</div>
<div class="abs divider"></div>
<div class="abs vdivider"></div>

<table class="abs cal">
  <caption>◂ &nbsp;&nbsp;&nbsp;&nbsp;&nbsp;&nbsp;&nbsp; April 2011 &nbsp;&nbsp;&nbsp;&nbsp;&nbsp;&nbsp;&nbsp; ▸</caption>
  <tr><th>MON</th><th>TUE</th><th>WED</th><th>THU</th><th>FRI</th><th>SAT</th><th>SUN</th></tr>
  <tr><td class="off">28</td><td class="off">29</td><td class="off">30</td><td class="off">31</td><td>1</td><td>2</td><td>3</td></tr>
  <tr><td class="today">4</td><td>5</td><td class="sel">6</td><td>7</td><td>8</td><td>9</td><td>10</td></tr>
  <tr><td>11</td><td>12</td><td>13</td><td>14</td><td>15</td><td>16</td><td>17</td></tr>
  <tr><td>18</td><td>19</td><td>20</td><td>21</td><td>22</td><td>23</td><td>24</td></tr>
  <tr><td>25</td><td>26</td><td>27</td><td>28</td><td>29</td><td>30</td><td class="off">1</td></tr>
</table>

<form class="abs assist">
  <h3>Need Assistance?</h3>
  <span class="field" style="top:40px">Name</span><span class="input" style="top:37px"></span>
  <span class="field" style="top:61px">email ID</span><span class="input" style="top:58px"></span>
  <span class="field" style="top:83px">phone no</span><span class="input" style="top:80px"></span>
  <span class="field" style="top:105px">Address</span><span class="input" style="top:102px"></span>
  <span class="field" style="top:127px">Messagebox</span><span class="input" style="top:142px;left:12px;width:191px;height:50px"></span>
</form>
<div class="abs submit">Submit</div>

<h3 class="abs sec-title" style="left:174px;top:667px">Testimonials</h3>
<div class="abs quote">Lorem ipsum dolor sit amet, consectetuer adipiscing elit. Aenean commodo ligula eget dolor. Aenean massa. Cum sociis natoque"</div>
<div class="abs quote-by"><b>Relan</b><br><i>Relan student</i></div>

<div class="abs events">
  <h3 class="sec-title">News &amp; Events</h3>
  <div class="event" style="top:36px"><div class="thumb" role="img" aria-label="Photo of a bright smile"></div><p>Lorem ipsum dolor sit amet, consectetuer adipiscing elit. Aenean commodo ligula eget dolor.</p></div>
  <div class="event" style="top:93px"><div class="thumb" role="img" aria-label="Photo of a bright smile"></div><p>Lorem ipsum dolor sit amet, consectetuer adipiscing elit. Aenean commodo ligula eget dolor.</p></div>
</div>

<div class="abs unis"></div>
<div class="abs unis-tab">UNIVERSITIES</div>
<div class="badge" style="left:225px"></div>
<div class="badge" style="left:361px"></div>
<div class="badge" style="left:497px"></div>
<div class="badge" style="left:633px"></div>
<div class="badge" style="left:769px"></div>

<div class="abs footer-panel"></div>
<div class="fcol" style="left:198px"><h4>Company</h4><a>About us</a><a>Vision</a><a>Team</a><a>Success Stories</a></div>
<div class="fcol" style="left:325px"><h4>Student</h4><a>Tests</a><a>Educational Loans</a><a>Faqs</a></div>
<div class="fcol" style="left:455px"><h4>Why us</h4><a>Why Choose Us</a><a>Testimonials</a><a>Press Clips</a><a>Photo Gallery</a></div>
<div class="fcol" style="left:578px"><h4>Online</h4><a>Enquiry</a><a>Registration</a><a>Feedback</a></div>
<div class="fcol" style="left:682px"><h4>Contacts</h4><p>Lorem ipsum dolor<br>sit amet, consectetuer<br>adipiscing elit.<br>Aenean commodo</p></div>
<div class="fcol" style="left:796px"><h4>Follow Us</h4></div>
<span class="social" style="left:792px;top:1016px;background:#3b6fb0"></span>
<span class="social" style="left:826px;top:1016px;background:#6aa6d8"></span>
<span class="social" style="left:792px;top:1052px;background:#e07a1f"></span>
<span class="social" style="left:826px;top:1052px;background:#b8c4d0"></span>

<nav class="abs foot-links"><span>Home</span>|<span>About</span>|<span>Courses</span>|<span>Doctor Name</span>|<span>Faculty</span>|<span>FAQ</span>|<span>Patients</span>|<span>Contact</span></nav>
<p class="abs copy">Dental Website – Copyright © 2012</p>
</body>
</html>
```